RWT Fittings Ltd Business Cards

We need a business card with our business logo. We provide window and door installations on high-rises in west coast British Colombia, Canada.

I would like my business information and details on one side of the card, and the other side the company name with logo

Target Market(s)

General Contractors

Industry/Entity Type

Construction

Contact Information for Business Card

one side i want my company name and logo in the dark theme logo that i provided

Requirements
Must have
• Marco Peltieri, 16045518293, RWTFittings@mailbox-demo.com, 1407-5194 Linden Row Burnaby BC, V5H 2K9, Owner & Manager

```html
<!DOCTYPE html>
<html lang="en">
<head>
<meta charset="utf-8">
<title>RWT Fittings Ltd – Business Cards</title>
<link href="https://fonts.googleapis.com/css2?family=Roboto:wght@400;500;700&display=swap" rel="stylesheet">
<style>
  :root {
    --stage: #222222;
    --card-white: #ffffff;
    --brand-blue: #27a6e0;
    --brand-grey: #8e8e8e;
    --ink: #1c1c1c;
    --ink-soft: #333333;
    --wash-blue: #e3f1fb;
    --wash-grey: #efefef;
  }
  * { box-sizing: border-box; margin: 0; padding: 0; }
  html, body { width: 1200px; height: 780px; overflow: hidden; }
  body {
    background: var(--stage);
    font-family: "Roboto", sans-serif;
    position: relative;
  }
  .card {
    position: absolute;
    top: 242px;
    width: 525px;
    height: 300px;
    border-radius: 2px;
    overflow: hidden;
  }
  .card--contact { left: 50px; background: var(--card-white); }
  .card--brand { left: 625px; background: var(--brand-blue); }

  /* contact side */
  .contact__wash {
    position: absolute;
    left: 150px; top: 0;
    width: 170px; height: 300px;
    background: linear-gradient(180deg, var(--wash-grey) 0%, var(--wash-blue) 45%, rgba(227,241,251,0) 100%);
  }
  .contact__details {
    position: absolute;
    left: 34px; top: 36px;
  }
  .contact__accent {
    position: absolute;
    left: -34px; top: 4px;
    width: 22px; height: 30px;
    background: var(--brand-blue);
  }
  .contact__name {
    font-size: 31px;
    font-weight: 700;
    line-height: 1.1;
    color: var(--brand-grey);
  }
  .contact__name .first { color: var(--brand-blue); }
  .contact__role {
    font-size: 13px;
    font-weight: 500;
    color: var(--ink-soft);
    margin-top: 4px;
  }
  .contact__address {
    font-size: 13px;
    line-height: 1.45;
    color: var(--ink-soft);
    margin-top: 14px;
    font-style: normal;
  }
  .contact__line {
    display: flex;
    align-items: center;
    gap: 8px;
    font-size: 13px;
    color: var(--ink-soft);
    margin-top: 10px;
  }
  .contact__line + .contact__line { margin-top: 4px; }
  .contact__line svg { width: 13px; height: 13px; fill: var(--brand-blue); flex: none; }

  .wordmark {
    display: flex;
    align-items: center;
    gap: 12px;
    font-weight: 700;
    letter-spacing: 0.5px;
  }
  .wordmark__square { flex: none; }
  .wordmark--contact {
    position: absolute;
    right: 30px; bottom: 34px;
    font-size: 30px;
    color: var(--brand-blue);
  }
  .wordmark--contact .wordmark__square { width: 30px; height: 30px; background: var(--brand-blue); }
  .wordmark--brand {
    position: absolute;
    left: 50%; top: 50%;
    transform: translate(-50%, -50%);
    font-size: 38px;
    color: var(--ink);
    white-space: nowrap;
  }
  .wordmark--brand .wordmark__square { width: 38px; height: 38px; background: var(--ink); }
</style>
</head>
<body>
  <section class="card card--contact">
    <div class="contact__wash" role="img" aria-label="Faint pale backdrop tint behind the contact details"></div>
    <div class="contact__details">
      <span class="contact__accent"></span>
      <h1 class="contact__name"><span class="first">Marco</span> Peltieri</h1>
      <p class="contact__role">Owner &amp; Manager</p>
      <address class="contact__address">1407-5194 Linden Row<br>Burnaby BC, V5H 2K9</address>
      <p class="contact__line">
        <svg viewBox="0 0 24 24" aria-hidden="true"><path d="M6.6 10.8a15.1 15.1 0 0 0 6.6 6.6l2.2-2.2a1 1 0 0 1 1-.25 11.4 11.4 0 0 0 3.6.57 1 1 0 0 1 1 1V20a1 1 0 0 1-1 1A17 17 0 0 1 3 4a1 1 0 0 1 1-1h3.5a1 1 0 0 1 1 1c0 1.25.2 2.45.57 3.57a1 1 0 0 1-.25 1z"/></svg>
        1604 551 8293
      </p>
      <p class="contact__line">
        <svg viewBox="0 0 24 24" aria-hidden="true"><path d="M3 5h18a1 1 0 0 1 1 1v12a1 1 0 0 1-1 1H3a1 1 0 0 1-1-1V6a1 1 0 0 1 1-1zm9 7.2L20 7H4zM4 9v8h16V9l-8 5.2z"/></svg>
        RWTFittings@mailbox-demo.com
      </p>
    </div>
    <div class="wordmark wordmark--contact"><span class="wordmark__square"></span>RWT Fittings Ltd</div>
  </section>

  <section class="card card--brand">
    <div class="wordmark wordmark--brand"><span class="wordmark__square"></span>RWT Fittings Ltd</div>
  </section>
</body>
</html>
```